Coastline Premier Retreats Business Card Design

Design a business card for Coastline Premier Retreats. Look at the website for colors and reference. Card should have logo, name, title, office number, mobile number, email, URL and a tagline like, "Luxury Hotel & Resort Email Marketing" (This might change).

https://www.coastlinepremierretreats.example

The rest I will leave up to your imagination.

Contact Information for Business Card

Logo, name, title, office number, mobile number, email, URL and a tagline like, "Luxury Hotel & Resort Email Marketing" (This might change).

```html
<!DOCTYPE html>
<html lang="en">
<head>
<meta charset="utf-8">
<title>Coastline Premier Retreats Business Card</title>
<link rel="stylesheet" href="https://fonts.googleapis.com/css2?family=Open+Sans:wght@400;600;700&display=swap">
<style>
  :root {
    --backdrop: #232323;
    --card: #1f1f22;
    --orange: #f07020;
    --white: #ffffff;
    --soft-white: #e9e9ea;
  }
  * { box-sizing: border-box; margin: 0; padding: 0; }
  html, body {
    width: 1200px; height: 780px; overflow: hidden;
    background: var(--backdrop);
    font-family: "Open Sans", Arial, sans-serif;
  }
  .canvas {
    position: relative; width: 1200px; height: 780px;
    display: flex; align-items: center; justify-content: center; gap: 40px;
  }
  .card {
    position: relative; width: 540px; height: 310px;
    background: var(--card);
    box-shadow: 0 18px 40px rgba(0,0,0,.45);
    overflow: hidden;
  }
  /* Front */
  .wordmark {
    position: absolute; top: 34px; left: 36px;
    color: var(--white); font-weight: 700; font-size: 21px; letter-spacing: .5px;
    display: flex; align-items: center; gap: 10px;
  }
  .wordmark-square { width: 12px; height: 12px; background: var(--orange); }
  .tagline {
    position: absolute; top: 84px; left: 36px;
    color: var(--orange); font-size: 13px; line-height: 1.4;
  }
  .contacts {
    position: absolute; left: 36px; bottom: 32px;
    list-style: none; color: var(--soft-white); font-size: 12.5px; line-height: 1.65;
  }
  .contacts li { display: flex; align-items: center; gap: 9px; }
  .contacts svg { width: 12px; height: 12px; flex: none; }
  .person {
    position: absolute; right: 44px; top: 150px; text-align: right;
  }
  .person-name { font-size: 27px; font-weight: 700; color: var(--white); line-height: 1.1; }
  .person-name .first { color: var(--orange); }
  .person-title { font-size: 14px; color: var(--soft-white); margin-top: 4px; }
  .edge-bar {
    position: absolute; right: 0; top: 148px; width: 16px; height: 68px;
    background: var(--orange);
  }
  /* Back */
  .card-back { display: flex; align-items: center; justify-content: center; }
  .back-wordmark {
    color: var(--white); font-weight: 700; font-size: 30px; letter-spacing: .5px;
    display: flex; align-items: center; gap: 14px;
  }
  .back-wordmark .wordmark-square { width: 16px; height: 16px; }
</style>
</head>
<body>
<main class="canvas">
  <section class="card card-front" aria-label="Business card front">
    <div class="wordmark"><span class="wordmark-square"></span>Coastline Premier Retreats</div>
    <p class="tagline">Luxury Hotel &amp;<br>Resort Email Marketing</p>
    <ul class="contacts">
      <li>
        <svg viewBox="0 0 24 24" aria-hidden="true"><path fill="#f07020" d="M6.6 10.8a15 15 0 0 0 6.6 6.6l2.2-2.2a1 1 0 0 1 1-.25 11.4 11.4 0 0 0 3.6.57 1 1 0 0 1 1 1V20a1 1 0 0 1-1 1A17 17 0 0 1 3 4a1 1 0 0 1 1-1h3.5a1 1 0 0 1 1 1c0 1.25.2 2.45.57 3.57a1 1 0 0 1-.25 1z"/></svg>
        (555) 014-2758
      </li>
      <li>
        <svg viewBox="0 0 24 24" aria-hidden="true"><rect x="6" y="2" width="12" height="20" rx="2" fill="none" stroke="#f07020" stroke-width="2"/><circle cx="12" cy="18" r="1.3" fill="#f07020"/></svg>
        (555) 019-7777
      </li>
      <li>
        <svg viewBox="0 0 24 24" aria-hidden="true"><circle cx="12" cy="12" r="9" fill="none" stroke="#f07020" stroke-width="2"/><path d="M3 12h18M12 3c3 3 3 15 0 18M12 3c-3 3-3 15 0 18" fill="none" stroke="#f07020" stroke-width="1.6"/></svg>
        www.coastlinepremierretreats.example
      </li>
      <li>
        <svg viewBox="0 0 24 24" aria-hidden="true"><rect x="2" y="5" width="20" height="14" rx="2" fill="#f07020"/><path d="M3 6l9 7 9-7" fill="none" stroke="#1f1f22" stroke-width="2"/></svg>
        info@coastlinepremierretreats.example
      </li>
    </ul>
    <div class="person">
      <p class="person-name"><span class="first">Marta</span> Kolinska</p>
      <p class="person-title">Co-Founder</p>
    </div>
    <span class="edge-bar"></span>
  </section>

  <section class="card card-back" aria-label="Business card back">
    <div class="back-wordmark"><span class="wordmark-square"></span>Coastline Premier Retreats</div>
  </section>
</main>
</body>
</html>
```